Business Card Design - Amberfield Court

We are looking at a new design for our business cards that has a modern and professional look. We run a residential aged care facility focussing on the care of residents. The cards will be used for potential clients, consultants and business opportunities in this sector. Blue and white is our main colours and would to see these colours incorporated in the design.
Industry/Entity Type
Business
Contact Information for Business Card
Amberfield Court, Darren Walsh, dwalsh@amberfieldcourt.com.au, Finance Manager, 0472 639 208, BCom, 37 Marrabel Crescent, Brindle Vale, Qld 4093.
Look and feel
Each slider illustrates characteristics of the customer's brand and the style your logo design should communicate.

```html
<!DOCTYPE html>
<html lang="en">
<head>
<meta charset="utf-8">
<title>Amberfield Court – Business Card</title>
<link rel="stylesheet" href="https://fonts.googleapis.com/css2?family=Source+Sans+3:wght@400;600;700&display=swap">
<style>
  :root {
    --backdrop: #d9d6d1;
    --card-face: #eef1f3;
    --card-edge: #c9ced3;
    --navy: #1f3a4d;
    --name-blue: #1f3f5a;
    --ink: #2b2f33;
    --muted: #5d6266;
  }
  * { box-sizing: border-box; margin: 0; padding: 0; }
  html, body {
    width: 1200px;
    height: 969px;
    overflow: hidden;
    background: var(--backdrop);
    font-family: "Source Sans 3", Arial, sans-serif;
  }
  .canvas {
    position: relative;
    width: 1200px;
    height: 969px;
  }
  .business-card {
    position: absolute;
    left: 367px;
    top: 74px;
    width: 465px;
    height: 820px;
    border-radius: 22px;
    border: 1px solid var(--card-edge);
    background: linear-gradient(180deg, #f3f5f7 0%, var(--card-face) 100%);
    overflow: hidden;
    text-align: center;
    color: var(--ink);
  }
  .brand {
    position: absolute;
    top: 118px;
    left: 0;
    width: 100%;
    display: flex;
    justify-content: center;
    align-items: center;
    gap: 12px;
  }
  .brand-dot {
    width: 18px;
    height: 18px;
    border-radius: 50%;
    background: var(--navy);
  }
  .brand-name {
    font-size: 30px;
    font-weight: 600;
    color: var(--navy);
    line-height: 1;
  }
  .person-name {
    position: absolute;
    top: 230px;
    width: 100%;
    font-size: 28px;
    font-weight: 700;
    color: var(--name-blue);
  }
  .person-role {
    position: absolute;
    top: 266px;
    width: 100%;
    font-size: 21px;
    color: var(--muted);
  }
  .address {
    position: absolute;
    top: 328px;
    width: 100%;
    font-size: 21px;
    line-height: 29px;
    font-style: normal;
  }
  .contact-lines {
    position: absolute;
    top: 406px;
    width: 100%;
    font-size: 21px;
    line-height: 30px;
    list-style: none;
  }
  .care-illustration {
    position: absolute;
    left: 0;
    bottom: 0;
    width: 465px;
    height: 240px;
  }
</style>
</head>
<body>
  <main class="canvas">
    <section class="business-card">
      <div class="brand">
        <span class="brand-dot"></span>
        <h1 class="brand-name">Amberfield Court</h1>
      </div>

      <h2 class="person-name">Darren Walsh BCom</h2>
      <p class="person-role">Finance Manager</p>

      <address class="address">37 Marrabel Crescent<br>Brindle Vale, Qld 4093.</address>

      <ul class="contact-lines">
        <li>Tel : 0472 639 208</li>
        <li>dwalsh@amberfieldcourt.com.au</li>
        <li>www.amberfieldcourt.com.au</li>
      </ul>

      <svg class="care-illustration" viewBox="0 0 465 240" role="img" aria-label="Silhouette illustration of a carer with an elderly resident inside a dark blue dome">
        <path d="M0 240 A232.5 232.5 0 0 1 465 240 Z" fill="var(--navy)"/>
      </svg>
    </section>
  </main>
</body>
</html>
```